Create Website for new company called "Verdale Lodge 37"

Verdale Lodge 37 is a new business situated in Southwestern Colorado. We are creating a business that will rent out spaces where clients can grow their own marijuana. Picture a large green house with partitioned spaces that are secured by a lock. Best way to envision this would be to think of a storage business that rents out storage rooms. The difference is that we will be having the units inside a green house ( for growing purposes) Picture a small area that is secured by locks, Picture an area that has the ability to provide state of the art security, cameras etc. We want to focus our efforts on professionals, blue collar workers and end users of marijuana. Our emphasis is in the area of assisting those whom wish to grow their own plants. We want to provide them a safe facility in which to do that. . Keep in mind that we also build custom grow rooms at clients homes and provide a grow pod (lease these) where a small grow unit will be delivered and picked up from our clients whom want to lease a unit for a short amount of time. We have a business card ( just designed) and will send that information to those whom express an interests in this project. We want to be able to sign people up for our services by entering an agreement and signing the agreement while on the internet. We want to provide our services to those whom consume recreational and medical marijuana. This site will need to gather information I.e email addresses so that we can followup with offers. This is a tremendous opportunity for the right designer. We will be creating many more websites as other states come on line and make marijuana legal to consume. Use the business card model for a point of reference of how we envision the concept. That is a business card we just recently printed. The hands and the plant is our logo so far. Open to suggestions. There will be three levels of service. Bronze, Silver, Gold or Platinum. We will also have a retail biz down the road but not at the present time.

Target Market(s)

Ages 21-60

Industry/Entity Type

Medical

Logo Text

Verdale Lodge 37.

Number of Pages Required

5+ page

Requirements
Must have
• Clean appearance not to busy , easily navigable from link to link, page to page. Must have ability down the road to enter into a contractual agreement via the website. Must use our provided logo and example of that is on our business card that will be uploaded here shortly. We would like to have the colors that are on the business card however if you have suggestions or color schemes that you want us to consider that is okay.
Nice to have
• Nice to have a animation of seed to weed and how clients can save a tremendous amount of money growing their own cannabis. Nice to have testimonial page or feedback page. Have a membership component to website,
Should not have
• No flashing lights, etc. Not to busy in terms of animations.

```html
<!DOCTYPE html>
<html lang="en">
<head>
<meta charset="utf-8">
<title>Verdale Lodge 37</title>
<link rel="stylesheet" href="https://fonts.googleapis.com/css2?family=Roboto:wght@400;500;700&family=Roboto+Condensed:wght@400;700&display=swap">
<style>
:root{
  --green:#2f8f1f;
  --green-light:#4fb52c;
  --green-dark:#1f6e12;
  --green-text:#1e7e34;
  --ink:#333;
  --muted:#8a8a8a;
  --rule:#e3e3e3;
  --footer:#2b2b2b;
  --footer-deep:#1f1f1f;
  --footer-text:#9a9a9a;
}
*{margin:0;padding:0;box-sizing:border-box}
html,body{width:778px;height:1200px;overflow:hidden;background:#fff}
body{position:relative;font-family:Arial,Helvetica,sans-serif;color:var(--ink)}
.abs{position:absolute}
.top-line{left:0;top:0;width:778px;height:2px;background:var(--green)}
.brand{left:0;top:22px;width:778px;text-align:center}
.brand-name{font-family:"Roboto Condensed",Arial,sans-serif;font-weight:700;font-size:26px;color:#3a3a3a;letter-spacing:.5px;display:inline-flex;align-items:center;gap:7px}
.brand-mark{width:12px;height:12px;border-radius:50%;background:var(--green)}
.brand-tag{font-size:6px;color:#444;margin-top:2px}
.hero{left:0;top:102px;width:778px;height:340px;background:linear-gradient(180deg,#c9d6de 0%,#a9b9c2 30%,#7e9a72 55%,#4f8a2f 75%,#3c7a22 100%)}
.hero-shadow{left:0;top:442px;width:778px;height:14px;background:radial-gradient(ellipse at top,rgba(0,0,0,.18),rgba(0,0,0,0) 70%)}
.nav{left:64px;top:81px;width:650px;height:37px;background:linear-gradient(180deg,var(--green-light),var(--green) 60%,var(--green-dark));display:flex}
.nav a{font-family:Roboto,Arial,sans-serif;font-weight:500;font-size:9.5px;color:#fff;text-decoration:none;display:flex;align-items:center;justify-content:center;border-right:1px solid rgba(0,0,0,.15);height:100%}
.nav a:last-child{border-right:none}
.hero-title{left:0;top:276px;width:778px;text-align:center;font-family:"Roboto Condensed",Arial,sans-serif;font-weight:700;font-size:42px;color:#fff;text-shadow:0 1px 3px rgba(0,0,0,.35)}
.hero-rule{left:272px;top:328px;width:234px;height:2px;background:rgba(255,255,255,.75)}
.hero-sub{left:160px;top:342px;width:458px;text-align:center;font-family:Roboto,Arial,sans-serif;font-weight:500;font-size:9.5px;line-height:14.5px;color:#fff;text-shadow:0 1px 2px rgba(0,0,0,.4)}
.hero-arrows{left:351px;top:379px}
h2.section{font-family:Roboto,Arial,sans-serif;font-weight:400;font-size:14.5px;color:#333}
h2.section span{color:var(--green-text)}
.para{font-size:6.4px;line-height:12.8px;color:var(--muted)}
.photo{border:3px solid #fff;box-shadow:0 0 2px rgba(0,0,0,.35)}
.svc-title{font-size:7.2px;color:#333}
.read-link{font-size:7.2px;color:var(--green-text)}
.card{border:1px solid var(--rule);background:#fff}
.card-date{font-family:Roboto,Arial,sans-serif;font-weight:500;font-size:9px;color:var(--green-text);position:absolute;left:8px;top:14px}
.card-title{position:absolute;left:8px;top:36px;font-size:6.6px;line-height:12px;color:#444}
.card-text{position:absolute;left:8px;top:69px;width:184px;font-size:6.4px;line-height:12.2px;color:var(--muted)}
.card-btn{position:absolute;left:8px;top:129px;width:66px;height:20px;border:1px solid #ccc;font-size:6.6px;color:#666;display:flex;align-items:center;justify-content:center}
.hr{height:1px;background:var(--rule)}
.partners{left:65px;top:980px;width:649px;height:34px;display:flex;justify-content:space-around;align-items:center}
.partners span{font-family:"Roboto Condensed",Arial,sans-serif;font-weight:700;font-size:20px;color:#b3b3b3}
.footer{left:0;top:1045px;width:778px;height:117px;background:var(--footer)}
.footer-bottom{left:0;top:1162px;width:778px;height:38px;background:var(--footer-deep)}
.bottom-line{left:0;top:1198px;width:778px;height:2px;background:var(--green)}
.newsletter-label{left:235px;top:1070px;font-family:"Roboto Condensed",Arial,sans-serif;font-size:13px;color:#cfcfcf}
.newsletter-div{left:304px;top:1068px;width:1px;height:24px;background:#555}
.newsletter-text{left:314px;top:1069px;font-size:5.6px;line-height:12px;color:#bdbdbd}
.email-field{left:481px;top:1070px;width:190px;height:23px;background:#f2f2f2;display:flex;align-items:center;padding-left:8px;gap:6px;font-size:5px;color:#999}
.email-go{margin-left:auto;margin-right:10px}
.footer-rule{left:65px;top:1106px;width:649px;height:1px;background:#3d3d3d}
.contact{font-size:6.6px;line-height:11px;color:var(--footer-text)}
.copyright{left:0;top:1177px;width:778px;text-align:center;font-size:6.4px;color:#888}
</style>
</head>
<body>
<div class="abs top-line"></div>

<header>
  <div class="abs brand">
    <div class="brand-name"><span class="brand-mark"></span>Verdale Lodge 37</div>
    <div class="brand-tag">"supporting the care &amp; cultivation of cannabis"</div>
  </div>
</header>

<section class="abs hero" role="img" aria-label="Photo inside a polytunnel greenhouse with rows of young green plants"></section>
<div class="abs hero-shadow"></div>

<nav class="abs nav">
  <a style="width:80px">HOME</a>
  <a style="width:94px">ABOUT US</a>
  <a style="width:92px">SERVICES</a>
  <a style="width:84px">CLIENTS</a>
  <a style="width:77px">NEWS</a>
  <a style="width:116px">TESTIMONIALS</a>
  <a style="width:107px">CONTACT US</a>
</nav>

<h1 class="abs hero-title">VERDALE LODGE</h1>
<div class="abs hero-rule"></div>
<p class="abs hero-sub">IT IS A LONG ESTABLISHED FACT THAT A READER WILL BE DISTRACTED BY THE READABLE PAGE WHEN LOOKING AT ITS LAYOUT.</p>
<svg class="abs hero-arrows" width="76" height="32" viewBox="0 0 76 32" aria-label="Slide controls">
  <circle cx="17" cy="16" r="14.5" fill="none" stroke="#fff" stroke-width="2"/>
  <path d="M20 9 L13 16 L20 23" fill="none" stroke="#fff" stroke-width="2.4"/>
  <circle cx="57" cy="16" r="14.5" fill="none" stroke="#fff" stroke-width="2"/>
  <path d="M54 9 L61 16 L54 23" fill="none" stroke="#fff" stroke-width="2.4"/>
</svg>

<section class="welcome">
  <h2 class="abs section" style="left:65px;top:467px">WELCOME TO <span>VERDALE LODGE</span></h2>
  <p class="abs para" style="left:65px;top:493px;width:305px">It is a long established fact that a reader will be distracted by the readable content of a page when looking at its layout. The point of using Lorem Ipsum is that it has a more-or-less normal distribution of letters, as opposed to using 'Content here, content here', making it look like readable English. Many desktop sites still in their infancy. Various versions have evolved</p>
  <div class="abs photo" style="left:65px;top:555px;width:302px;height:130px;background:linear-gradient(180deg,#b9c4c9 0%,#8faa78 40%,#5f9a3a 65%,#d9d23a 100%)" role="img" aria-label="Photo of a greenhouse interior with beds of yellow flowers and green seedlings"></div>
  <div class="abs" style="left:75px;top:686px;width:282px;height:8px;background:radial-gradient(ellipse at top,rgba(0,0,0,.15),rgba(0,0,0,0) 70%)"></div>
</section>

<section class="services">
  <h2 class="abs section" style="left:401px;top:467px">OUR <span>SERVICES</span></h2>
  <svg class="abs" style="left:692px;top:471px" width="24" height="10" viewBox="0 0 24 10" aria-label="Previous and next">
    <path d="M5 2 L2 5 L5 8" fill="none" stroke="#aaa" stroke-width="1"/>
    <path d="M18 2 L21 5 L18 8" fill="none" stroke="#aaa" stroke-width="1"/>
  </svg>

  <div class="abs photo" style="left:402px;top:495px;width:93px;height:85px;background:linear-gradient(180deg,#cfd8d6,#8eb07a 55%,#4e8a2c)" role="img" aria-label="Photo of a small glass greenhouse on a lawn"></div>
  <div class="abs svc-title" style="left:510px;top:497px">NEQUE PORRO QUISQUAM EST QUI DOLOREM IPSUM</div>
  <p class="abs para" style="left:510px;top:512px;width:205px;line-height:12.2px">It is a long established fact that a reader will be distracted by the readable content of a page when looking at its layout. The point of using Lorem Ipsum is that it has a more-or-less normal distribution of content here', making it look like readable English....</p>
  <div class="abs read-link" style="left:510px;top:569px">[ READ MORE ]</div>
  <div class="abs hr" style="left:401px;top:591px;width:322px"></div>

  <div class="abs photo" style="left:402px;top:602px;width:93px;height:84px;background:linear-gradient(180deg,#b7cdd9,#7fa2b6 50%,#8f6a45)" role="img" aria-label="Photo of a wooden framed greenhouse door"></div>
  <div class="abs svc-title" style="left:510px;top:604px">NEQUE PORRO QUISQUAM EST QUI DOLOREM IPSUM</div>
  <p class="abs para" style="left:510px;top:618px;width:205px;line-height:12.2px">It is a long established fact that a reader will be distracted by the readable content of a page when looking at its layout. The point of using Lorem Ipsum is that it has a more-or-less normal distribution of content here', making it look like readable English....</p>
  <div class="abs read-link" style="left:510px;top:675px">[ READ MORE ]</div>
</section>

<div class="abs hr" style="left:65px;top:705px;width:649px"></div>

<section class="news">
  <h2 class="abs section" style="left:0;top:718px;width:778px;text-align:center">LATEST <span>NEWS</span></h2>
  <p class="abs" style="left:0;top:744px;width:778px;text-align:center;font-size:6.4px;color:var(--muted)">It is a long established fact that a reader will be distracted by the readable content of a page when looking at its layout.</p>

  <article class="abs card" style="left:65px;top:776px;width:198px;height:164px">
    <div class="card-date">10 NOVEMBER2014</div>
    <div class="card-title">NEQUE PORRO QUISQUAM EST QUI DOLOREM IPSUM<br>LOBORTIS SSIM ET AT QUAM.</div>
    <p class="card-text">It is a long established fact that a reader will be distracted by the readable content of a page when looking at its layout. The point of using Lorem Ipsum is that it has a more-or-less here, look like readable English.</p>
    <div class="card-btn">READ MORE</div>
  </article>
  <article class="abs card" style="left:290px;top:776px;width:199px;height:164px">
    <div class="card-date">10 NOVEMBER2014</div>
    <div class="card-title">NEQUE PORRO QUISQUAM EST QUI DOLOREM IPSUM<br>LOBORTIS SSIM ET AT QUAM.</div>
    <p class="card-text">It is a long established fact that a reader will be distracted by the readable content of a page when looking at its layout. The point of using Lorem Ipsum is that it has a more-or-less here, look like readable English.</p>
    <div class="card-btn">READ MORE</div>
  </article>
  <article class="abs card" style="left:514px;top:776px;width:199px;height:164px">
    <div class="card-date">10 NOVEMBER2014</div>
    <div class="card-title">NEQUE PORRO QUISQUAM EST QUI DOLOREM IPSUM<br>LOBORTIS SSIM ET AT QUAM.</div>
    <p class="card-text">It is a long established fact that a reader will be distracted by the readable content of a page when looking at its layout. The point of using Lorem Ipsum is that it has a more-or-less here, look like readable English.</p>
    <div class="card-btn">READ MORE</div>
  </article>
</section>

<div class="abs hr" style="left:65px;top:965px;width:649px"></div>
<div class="abs partners">
  <span>Fenmoor</span><span>Quilby</span><span>Orvane</span><span>Lumetta</span><span>Skelbrook</span><span>Harrowen</span>
</div>
<div class="abs hr" style="left:65px;top:1026px;width:649px"></div>

<footer>
  <div class="abs footer"></div>
  <svg class="abs" style="left:93px;top:1068px" width="122" height="20" viewBox="0 0 122 20" aria-label="Social links">
    <g fill="none" stroke="#bdbdbd" stroke-width="1">
      <circle cx="11" cy="10" r="9"/><circle cx="36" cy="10" r="9"/><circle cx="60" cy="10" r="9"/><circle cx="85" cy="10" r="9"/><circle cx="109" cy="10" r="9"/>
    </g>
  </svg>
  <div class="abs newsletter-label">NewsLetter :</div>
  <div class="abs newsletter-div"></div>
  <div class="abs newsletter-text">In venenatis neque a eros laoreet eu placerat erat suscipit.<br>Fusce cursus, erat ut scelerisque condimentum</div>
  <div class="abs email-field">
    <svg width="12" height="8" viewBox="0 0 12 8"><rect x=".5" y=".5" width="11" height="7" fill="#bbb"/><path d="M.5 .5 L6 4.5 L11.5 .5" fill="none" stroke="#f2f2f2" stroke-width="1"/></svg>
    <span>Enter Your Email Address :</span>
    <svg class="email-go" width="6" height="10" viewBox="0 0 6 10"><path d="M1 1 L5 5 L1 9" fill="none" stroke="#999" stroke-width="1"/></svg>
  </div>
  <div class="abs footer-rule"></div>

  <svg class="abs" style="left:82px;top:1123px" width="14" height="15" viewBox="0 0 14 15"><rect x="1" y="1" width="12" height="13" fill="#8a8a8a"/><rect x="4" y="4" width="2" height="2" fill="#2b2b2b"/><rect x="8" y="4" width="2" height="2" fill="#2b2b2b"/><rect x="5" y="9" width="4" height="5" fill="#2b2b2b"/></svg>
  <div class="abs contact" style="left:105px;top:1122px">Address :418 Fernbrook Lane Unit 7<br>55514</div>

  <svg class="abs" style="left:277px;top:1123px" width="16" height="16" viewBox="0 0 16 16"><path d="M3 1 L6 4 L4.5 6 C6 9 7.5 10.5 10 11.5 L12 10 L15 13 L12.5 15.5 C6 14 2 10 0.5 3.5 Z" fill="#8a8a8a"/></svg>
  <div class="abs contact" style="left:302px;top:1126px">Phone : (555)-204-3719</div>

  <svg class="abs" style="left:444px;top:1122px" width="16" height="16" viewBox="0 0 16 16"><rect x="1" y="5" width="14" height="10" fill="#8a8a8a"/><rect x="4" y="1" width="8" height="5" fill="#8a8a8a" stroke="#2b2b2b" stroke-width=".8"/><rect x="4" y="8" width="8" height="1.2" fill="#2b2b2b"/><rect x="4" y="11" width="8" height="1.2" fill="#2b2b2b"/></svg>
  <div class="abs contact" style="left:470px;top:1126px">Fax :(555)-204-3720</div>

  <svg class="abs" style="left:583px;top:1125px" width="15" height="10" viewBox="0 0 15 10"><rect x="0" y="0" width="15" height="10" fill="#8a8a8a"/><path d="M0 0 L7.5 5.5 L15 0" fill="none" stroke="#2b2b2b" stroke-width="1"/></svg>
  <div class="abs contact" style="left:607px;top:1126px">Email : hello@verdalelodge37.com</div>

  <div class="abs footer-bottom"></div>
  <div class="abs copyright">© Copy Rights 2014 Verdale Lodge 37 All Right Reserved.</div>
  <div class="abs bottom-line"></div>
</footer>
</body>
</html>
```